Anzeigengestaltung für eine Hausarztpraxis
Zielgruppe
Wir sind eine Hausarztpraxis mit zwei Standorten und suchen eine Ärztin oder einen Arzt zur Anstellung in der klassischen Hausarzt Medizin am Standort Erlenbrunn
Aufgabenstellung
Bitte beachtet den Text im Anhang, der ist schon vorgegeben. (Anzeigentext)
Wir suchen ein ruhiges, hochwertiges Layout für eine Stellenanzeige einer Hausarztpraxis in einem historischen Gebäude.
Der Text steht im Vordergrund, das Design soll zurückhaltend, klar und wertig sein.
Bitte keine Icons, keine bunten Farben, keine verspielten Elemente.
Gerne viel Weissraum, klare Typografie, ruhige Anmutung.
Schrift: Garamond für den Fliesstext (bereits gewählt).
Das Layout soll sowohl als PDF wie auch online funktionieren.
Optional: ein sehr dezentes grafisches Element oder eine ruhige Bildanmutung (z. B. Struktur, Licht, Architekturdetail).

```html
<!DOCTYPE html>
<html lang="de">
<head>
<meta charset="utf-8">
<title>Stellenanzeige – Arztpraxis Lindenhof Erlenbrunn</title>
<link rel="stylesheet" href="https://fonts.googleapis.com/css2?family=EB+Garamond:ital,wght@0,400;0,600;0,700;1,400&display=swap">
<style>
  :root {
    --ink: #2b2a24;
    --accent: #8cb826;
    --paper: #ffffff;
    --frame: #d9d9d9;
  }
  html, body {
    margin: 0;
    padding: 0;
    width: 846px;
    height: 1200px;
    overflow: hidden;
    background: var(--paper);
  }
  .ad {
    position: relative;
    width: 846px;
    height: 1200px;
    box-sizing: border-box;
    border: 1px solid var(--frame);
    font-family: "EB Garamond", Garamond, serif;
    color: var(--ink);
  }
  .brand {
    position: absolute;
    top: 112px;
    left: 0;
    width: 100%;
    display: flex;
    justify-content: center;
    align-items: center;
    gap: 12px;
  }
  .brand__dot {
    width: 14px;
    height: 14px;
    border-radius: 50%;
    background: var(--ink);
  }
  .brand__name {
    font-size: 30px;
    font-weight: 700;
    line-height: 1;
  }
  .content {
    position: absolute;
    top: 252px;
    left: 56px;
    width: 740px;
  }
  .headline {
    margin: 0;
    font-size: 28.5px;
    font-weight: 700;
    line-height: 34px;
    white-space: nowrap;
  }
  .motto {
    margin: 19px 0 20px;
    text-align: center;
    font-style: italic;
    font-size: 20.5px;
    line-height: 27px;
  }
  .copy p,
  .copy h2,
  .contact-mail {
    font-size: 17.4px;
    line-height: 23.3px;
    white-space: nowrap;
  }
  .copy p {
    margin: 0 0 23.3px;
  }
  .copy h2 {
    margin: 0;
    font-weight: 700;
  }
  .contact-mail {
    margin: 0 0 20px;
    font-weight: 700;
  }
  .address {
    font-style: normal;
    font-size: 19.5px;
    line-height: 26.2px;
  }
  .address__name {
    color: var(--accent);
    font-weight: 600;
  }
</style>
</head>
<body>
  <article class="ad">
    <header class="brand">
      <span class="brand__dot"></span>
      <span class="brand__name">Arztpraxis Lindenhof</span>
    </header>

    <section class="content">
      <h1 class="headline">Hausarztmedizin mit Tiefe –<br>dort, wo man noch echte Grundversorgung lebt</h1>

      <p class="motto">Ein Ort, der trägt. Ein Team, das bleibt.<br>Eine Arbeit, die Wertschätzung hat.</p>

      <div class="copy">
        <p>Manche Orte verändern die Art, wie man arbeitet. Unsere Praxis in Erlenbrunn ist so ein Ort.<br>
        In einem historischen Gebäude gelegen, mit grosszügigem Ambiente, warmen Vertäfelungen und<br>
        kunstvoller Wandbemalung, entstehen hier Behandlungsräume von Ruhe und Würde. Kein steriler<br>
        Praxisalltag, sondern ein Ort, der Gespräche trägt und medizinische Arbeit unterstützt.</p>

        <p>Für diesen besonderen Ort suchen wir eine Hausärztin oder einen Hausarzt, die oder der nicht<br>
        einfach einen Arbeitsplatz sucht, sondern einen Platz, an dem Medizin menschlich sein darf.</p>

        <h2>Ein Team mit Haltung</h2>
        <p>Sie arbeiten in einem freundlichen, über Jahre gewachsenen Team mit hoher personeller<br>
        Kontinuität und geringer Fluktuation.</p>

        <h2>Zeit für gute Medizin</h2>
        <p>Unsere Patientinnen und Patienten sind überwiegend gut bis sehr gut situiert, wertschätzend und<br>
        therapieoffen. Das ermöglicht ruhiges, strukturiertes Arbeiten mit Fokus auf Qualität, Beziehung<br>
        und nachhaltige Behandlung.</p>

        <h2>Und sonst?</h2>
        <p>Der Praxisalltag ist klar strukturiert, ruhig und verlässlich. Geregelte und in Abstimmung flexible<br>
        Arbeitszeiten ohne Wochenend- oder Nachtdienste, eine sehr gute leistungsbezogene Vergütung<br>
        sowie ein respektvoller, wertschätzender Umgang auf Augenhöhe schaffen ein Umfeld, in dem man<br>
        sich auf die medizinische Arbeit konzentrieren und langfristig wohlfühlen kann.</p>

        <p>Wir freuen uns über eine unkomplizierte Kontaktaufnahme per E-Mail oder Telefon – gerne auch<br>
        ganz unverbindlich und ohne vollständige Bewerbungsunterlagen.</p>
      </div>

      <p class="contact-mail">E-Mail: Helga.Weissmoor@praxis-lindenhof.ch</p>

      <address class="address">
        <span class="address__name">Arztpraxis Lindenhof</span><br>
        Mühlegasse 7<br>
        4712 Erlenbrunn<br>
        Tel: 0621487305
      </address>
    </section>
  </article>
</body>
</html>
```